Brightfen Business Card Redesign & Logo Update

We need to update our business cards to something more modern and fresh. Brightfen can provide the current color schemes and old design examples, but welcome creativity in helping us with this redesign. PLEASE NOTE that we no longer utilize the "tree" and/or "leaf" imagery in our branding. If able would apprecaite an update on the quality of our "words only" logo in Ai. / PNG formats too.

Target Market(s)

Investors, landowners, corporate partners, contractors

Industry/Entity Type

Environmental Restoration & Conservation

Contact Information for Business Card

Logo, persons name, title, mailing address, phone and email, website url

Font styles to use
Other font styles liked:
• Merriweather

Requirements
Nice to have
• Logo, persons name, title, mailing address, phone and email, website url, but open to ideams
Should not have
• No all back backgrounds

```html
<!DOCTYPE html>
<html lang="en">
<head>
<meta charset="utf-8">
<title>Brightfen Business Card</title>
<link href="https://fonts.googleapis.com/css2?family=Lato:wght@400;700;900&display=swap" rel="stylesheet">
<style>
  :root {
    --stage: #2e2e2e;
    --green: #137c37;
    --green-dark: #0f6a2e;
    --orange: #ee7d0e;
    --ink: #333333;
    --paper: #ffffff;
  }
  * { margin: 0; padding: 0; box-sizing: border-box; }
  html, body { width: 1200px; height: 875px; overflow: hidden; }
  body {
    background: var(--stage);
    font-family: "Lato", sans-serif;
    display: flex;
    align-items: center;
    justify-content: center;
    gap: 40px;
  }
  .card {
    position: relative;
    width: 540px;
    height: 309px;
    border-radius: 18px;
    overflow: hidden;
  }
  .card-front {
    background: var(--green);
    display: flex;
    align-items: center;
    justify-content: center;
  }
  .front-texture {
    position: absolute;
    inset: 0;
    background: radial-gradient(circle at 40% 45%, var(--green) 0%, var(--green-dark) 100%);
  }
  .front-wordmark {
    position: relative;
    color: var(--paper);
    font-weight: 900;
    font-size: 76px;
    letter-spacing: 2px;
    text-transform: uppercase;
  }
  .card-back { background: var(--paper); }
  .back-wordmark {
    position: absolute;
    left: 36px;
    top: 58px;
    color: var(--green);
    font-weight: 900;
    font-size: 40px;
    letter-spacing: 1px;
    text-transform: uppercase;
  }
  .holder {
    position: absolute;
    right: 36px;
    top: 66px;
    text-align: right;
  }
  .holder-name {
    color: var(--green);
    font-weight: 700;
    font-size: 21px;
    letter-spacing: 0.5px;
    text-transform: uppercase;
  }
  .holder-title {
    color: var(--orange);
    font-size: 13px;
    margin-top: 2px;
  }
  .contact-list {
    position: absolute;
    left: 38px;
    top: 128px;
    list-style: none;
    color: var(--ink);
    font-size: 12px;
    line-height: 17px;
  }
  .contact-list li {
    display: flex;
    align-items: flex-start;
    gap: 9px;
  }
  .contact-list svg {
    width: 11px;
    height: 11px;
    margin-top: 3px;
    flex: none;
    fill: var(--green);
  }
  .contact-list .address svg { margin-top: 11px; }
  .back-bands {
    position: absolute;
    left: 0;
    bottom: 0;
    width: 540px;
    height: 40px;
  }
</style>
</head>
<body>
  <section class="card card-front">
    <div class="front-texture" role="img" aria-label="Faint cracked-earth texture in deep green"></div>
    <div class="front-wordmark">Brightfen</div>
  </section>

  <section class="card card-back">
    <div class="back-wordmark">Brightfen</div>

    <div class="holder">
      <div class="holder-name">Daniel Reyes</div>
      <div class="holder-title">Founder &amp; CEO</div>
    </div>

    <ul class="contact-list">
      <li class="address">
        <svg viewBox="0 0 12 12"><path d="M6 0a4 4 0 0 0-4 4c0 3 4 8 4 8s4-5 4-8a4 4 0 0 0-4-4zm0 5.6A1.6 1.6 0 1 1 6 2.4a1.6 1.6 0 0 1 0 3.2z"/></svg>
        <span>123 Anywhere St<br>Any City, State 12345</span>
      </li>
      <li>
        <svg viewBox="0 0 12 12"><path d="M2.5 0.5l2 2.5-1.2 1.4c.8 1.7 2.1 3 3.8 3.8L8.5 7l2.5 2-1.2 2.2C5 11 1 7 .8 1.7z"/></svg>
        <span>(123) 456-7890</span>
      </li>
      <li>
        <svg viewBox="0 0 12 12"><path d="M3 0h6a1 1 0 0 1 1 1v10a1 1 0 0 1-1 1H3a1 1 0 0 1-1-1V1a1 1 0 0 1 1-1zm.6 1.4v8h4.8v-8zM6 10.2a.6.6 0 1 0 0 1.2.6.6 0 0 0 0-1.2z"/></svg>
        <span>(123) 456-7890</span>
      </li>
      <li>
        <svg viewBox="0 0 12 12"><path d="M3 0h6v3H3zM1 4h10a1 1 0 0 1 1 1v4h-2v3H2V9H0V5a1 1 0 0 1 1-1zm2.2 4.6v2.2h5.6V8.6z"/></svg>
        <span>(123) 456-7890</span>
      </li>
      <li>
        <svg viewBox="0 0 12 12"><path d="M0 2h12v1L6 7 0 3zm0 2.4l6 4 6-4V10H0z"/></svg>
        <span>hello@yourwebsite.com</span>
      </li>
      <li>
        <svg viewBox="0 0 12 12"><path d="M6 0a6 6 0 1 0 0 12A6 6 0 0 0 6 0zm0 1.3c.8 0 1.6 1.7 1.8 4H4.2c.2-2.3 1-4 1.8-4zM4.2 6.7h3.6c-.2 2.3-1 4-1.8 4s-1.6-1.7-1.8-4z"/></svg>
        <span>www.yourwebsite.com</span>
      </li>
    </ul>

    <svg class="back-bands" viewBox="0 0 540 40" aria-hidden="true">
      <polygon points="0,30 408,30 408,40 0,40" fill="var(--orange)"/>
      <polygon points="404,10 410,10 410,40 404,40" fill="var(--orange)"/>
      <polygon points="414,6 540,0 540,40 414,40" fill="var(--green)"/>
      <rect x="410" y="10" width="4" height="30" fill="var(--paper)"/>
    </svg>
  </section>
</body>
</html>
```